Brightmoor Lift Inc Website Deisgn

We are a new small elevator contracting company.
We would like a full website designed similar to
http://pellingtonlifts.com or https://www.northvalelifting.ca/
In addition to contents found on the above webpages.. we would like a section for project gallery etc.... have fun with it ... make it professional

Target Market(s)

Elevator Consultants - Property managers - Condo Boards - Commercial office buildings

Coding

Number of Pages Required

5+ page

Requirements
Must have
• Navigation Bar.. Be view able via mobile ..Should be pictures of Tall Office buildings in background.. Toronto city skyline etc....

Have Fun!

```html
<!DOCTYPE html>
<html lang="en">
<head>
<meta charset="utf-8">
<title>Brightmoor Lift Inc – Website Design</title>
<link rel="stylesheet" href="https://fonts.googleapis.com/css2?family=Rubik:wght@500;700;800;900&family=Quicksand:wght@400;500;600&display=swap">
<style>
:root{
  --navy:#0b2350;
  --red:#c8283a;
  --footer:#0e0d2e;
  --page:#f2f2f4;
  --soft:#f5f5f7;
  --white:#ffffff;
  --text:#3a3a48;
  --line:#d3d3da;
  --divider:#2b2a4a;
  --head:"Rubik",sans-serif;
  --body:"Quicksand",sans-serif;
}
*{box-sizing:border-box;margin:0;padding:0}
html,body{width:1200px;height:3035px;overflow:hidden}
body{background:var(--page);font-family:var(--body);color:var(--text);position:relative}
.abs{position:absolute}

.brand-hero{position:absolute;left:0;top:112px;width:1200px;height:136px;display:flex;align-items:center;justify-content:center}
.brand-hero .name{font-family:var(--head);font-weight:800;font-size:60px;color:var(--navy);letter-spacing:1px;text-transform:uppercase}

.mark{display:flex;align-items:center;font-family:var(--head);font-weight:700;color:var(--navy);white-space:nowrap}
.mark.light{color:var(--white)}

.board{position:absolute;background:var(--white);overflow:hidden;box-shadow:0 2px 10px rgba(0,0,0,.05)}
.desktop{left:350px;top:381px;width:764px;height:2551px}
.mobile{left:85px;top:381px;width:179px;height:2434px}

.photo{position:absolute}
.hero-photo{background:linear-gradient(155deg,#6f8aa6 0%,#2b5a86 35%,#1f4f7c 60%,#3b79a8 100%)}

.tag{position:absolute;font-family:var(--head);color:var(--white);display:flex;align-items:center;padding-left:12px;white-space:nowrap}
.tag.red{background:var(--red)}
.tag.navy{background:var(--navy)}

.btn{position:absolute;display:flex;align-items:center;justify-content:center;color:var(--white);font-family:var(--body);font-weight:500;border-radius:3px}
.btn.navy{background:var(--navy)}
.btn.red{background:var(--red)}

.sec-title{position:absolute;left:0;width:100%;text-align:center;font-family:var(--head);font-weight:800;color:var(--navy)}
.sec-title em{font-style:normal;color:var(--red)}
.sec-lead{position:absolute;text-align:center;color:var(--text)}

.card{position:absolute;background:var(--white);border:1px solid var(--line);border-radius:6px 6px 0 0;overflow:hidden;text-align:center}
.card .pic{width:100%}
.card h3{font-family:var(--head);font-weight:700;color:#111}
.card p{color:var(--text)}
.card .more{color:var(--red);font-weight:600;display:block}

.pic-modern{background:linear-gradient(180deg,#2a2320,#5a3a22 45%,#1a1716)}
.pic-maint{background:linear-gradient(135deg,#7d8fa6,#a9b6c6 50%,#5f7088)}
.pic-repair{background:linear-gradient(180deg,#1d2f57,#3b4f79 50%,#223258)}
.pic-other{background:linear-gradient(160deg,#3b3e46,#8d8f94 50%,#b63a3a)}

.gallery{position:absolute;display:grid;box-shadow:0 10px 30px rgba(0,0,0,.18)}
.g1{background:linear-gradient(160deg,#5a4636,#8a6a4e 60%,#3c2e25)}
.g2{background:linear-gradient(180deg,#9aa2ad,#2c2f36 60%,#555b64)}
.g3{background:linear-gradient(160deg,#b57b4c,#e3a674 55%,#6b4630)}
.g4{background:linear-gradient(180deg,#7c4e64,#b27e8f 55%,#5a3a4b)}
.g5{background:linear-gradient(180deg,#2c3a3c,#516667 50%,#1c2326)}
.g-cta{background:linear-gradient(160deg,#2a4c7c,#0b2350);display:flex;align-items:center;justify-content:center;text-align:center;color:var(--white);font-family:var(--head);font-weight:800}

.field{position:absolute;border:1px solid #b9bcc6;border-radius:4px;color:#777;display:flex;align-items:flex-start;background:var(--white)}

.footer{position:absolute;left:0;background:var(--footer);color:var(--white)}
.about{position:absolute;background:var(--white);color:#222;border-radius:4px}
.about h4{font-family:var(--head);font-weight:700}
.f-col{position:absolute}
.f-col h4{font-family:var(--body);font-weight:600}
.f-col ul{list-style:none}
.contact-row{position:absolute;display:flex;align-items:flex-start;white-space:nowrap}
.contact-row svg{flex:none}

.desktop .topline{position:absolute;font-size:10px}
.desktop .topline .label{color:var(--red);font-size:7px;letter-spacing:1px}
.nav{position:absolute;left:96px;top:43px;width:573px;height:28px;background:var(--navy);border-radius:4px;display:flex;align-items:center;padding-left:69px;gap:37px;font-size:8.5px;color:#e8ebf3}
.nav .active{color:var(--red);position:relative;height:28px;display:flex;align-items:center}
.nav .active::after{content:"";position:absolute;left:-2px;right:-2px;bottom:0;height:2px;background:var(--red)}

.desktop .card h3{font-size:16px;margin:33px 0 20px}
.desktop .card p{font-size:8.5px;line-height:13px;padding:0 20px}
.desktop .card .more{font-size:8px;margin-top:13px}
.desktop .field{height:26px;padding:8px 9px;font-size:8px}

.mobile .card h3{font-size:11.5px;margin:11px 0 9px}
.mobile .card p{font-size:6px;line-height:10px;padding:0 8px}
.mobile .card .more{font-size:6px;margin-top:8px}
.mobile .field{left:10px;width:160px;height:22px;padding:6px 7px;font-size:6px}
</style>
</head>
<body>

<header class="brand-hero">
  <span class="name">Brightmoor Lift Inc</span>
</header>

<section class="board mobile" aria-label="Mobile layout">
  <div class="abs" style="left:0;top:0;width:179px;height:22px;background:var(--white)">
    <div class="mark abs" style="left:10px;top:6px;font-size:7px">Brightmoor Lift Inc</div>
    <div class="abs" style="left:158px;top:6px;width:11px;height:11px;background:var(--red);border-radius:2px">
      <svg width="11" height="11" viewBox="0 0 11 11"><path d="M3 4h5M3 5.5h5M3 7h5" stroke="#fff" stroke-width=".8"/></svg>
    </div>
  </div>
  <div class="photo hero-photo" role="img" aria-label="Looking up at tall glass office towers against a blue sky" style="left:0;top:22px;width:179px;height:247px"></div>
  <div class="tag red" style="left:10px;top:88px;width:43px;height:14px;font-size:7px;padding-left:4px;font-weight:500">Welcome</div>
  <div class="tag navy" style="left:10px;top:106px;width:162px;height:20px;font-size:12.5px;padding-left:4px;font-weight:800;letter-spacing:.6px">Brightmoor Lift</div>
  <div class="tag red" style="left:10px;top:128px;width:38px;height:21px;font-size:13px;padding-left:4px;font-weight:800;letter-spacing:.6px">INC</div>
  <div class="btn navy" style="left:10px;top:186px;width:55px;height:17px;font-size:6px">Free Quote</div>
  <div class="btn red" style="left:69px;top:186px;width:55px;height:17px;font-size:6px">Contact Us</div>

  <h2 class="sec-title" style="top:296px;font-size:15.5px"><em>Services</em> We Offer</h2>
  <p class="sec-lead" style="left:10px;top:329px;width:160px;font-size:6px;line-height:10px">Lorem ipsum dolor sit amet, consectetur an adipiscing elit, sed do eiusmod tempor incididunt ut labore man et dolore magna aliqua.</p>

  <article class="card" style="left:10px;top:372px;width:160px;height:188px">
    <div class="pic pic-modern" role="img" aria-label="Modern building lobby at night" style="height:73px"></div>
    <h3>Modernization</h3>
    <p>Lorem ipsum dolor sit amet, consectetur adipiscing elit, sed do eiusmod tempor incididunt ut labore et dolore magna aliqua. Ut enim ad minim veniam, quis nostrud exercitation...</p>
    <span class="more">Free Quote</span>
  </article>
  <article class="card" style="left:10px;top:575px;width:160px;height:187px">
    <div class="pic pic-maint" role="img" aria-label="Technician working on a glass facade" style="height:73px"></div>
    <h3>Maintenance</h3>
    <p>Lorem ipsum dolor sit amet, consectetur adipiscing elit, sed do eiusmod tempor incididunt ut labore et dolore magna aliqua. Ut enim ad minim veniam, quis nostrud exercitation...</p>
    <span class="more">Free Quote</span>
  </article>
  <article class="card" style="left:10px;top:777px;width:160px;height:187px">
    <div class="pic pic-repair" role="img" aria-label="Wall rack of wrenches" style="height:73px"></div>
    <h3>Repairing</h3>
    <p>Lorem ipsum dolor sit amet, consectetur adipiscing elit, sed do eiusmod tempor incididunt ut labore et dolore magna aliqua. Ut enim ad minim veniam, quis nostrud exercitation...</p>
    <span class="more">Free Quote</span>
  </article>
  <article class="card" style="left:10px;top:978px;width:160px;height:188px">
    <div class="pic pic-other" role="img" aria-label="Red ratchet tools on a workbench" style="height:73px"></div>
    <h3>Other Services</h3>
    <p>Lorem ipsum dolor sit amet, consectetur adipiscing elit, sed do eiusmod tempor incididunt ut labore et dolore magna aliqua. Ut enim ad minim veniam, quis nostrud exercitation...</p>
    <span class="more">Free Quote</span>
  </article>

  <div class="abs" style="left:0;top:1195px;width:179px;height:369px;background:var(--soft)"></div>
  <h2 class="sec-title" style="top:1222px;font-size:15.5px"><em>Our Project</em> Gallery</h2>
  <p class="sec-lead" style="left:10px;top:1255px;width:160px;font-size:6px;line-height:10px">Lorem ipsum dolor sit amet, consectetur an adipiscing elit, sed do eiusmod tempor incididunt ut labore man et dolore magna aliqua.</p>
  <div class="gallery" style="left:10px;top:1299px;width:160px;height:254px;grid-template-columns:1fr 1fr;grid-template-rows:repeat(3,1fr)">
    <div class="g1" role="img" aria-label="Elevator lobby with wood panelling"></div>
    <div class="g2" role="img" aria-label="Downtown skyscrapers"></div>
    <div class="g4" role="img" aria-label="Residential tower balconies"></div>
    <div class="g3" role="img" aria-label="Warm-lit elevator hallway"></div>
    <div class="g5" role="img" aria-label="Apartment block facade"></div>
    <div class="g-cta" style="font-size:9px;line-height:12px">View Project<br>Detail</div>
  </div>

  <h2 class="sec-title" style="top:1607px;font-size:15.5px"><em>Contact</em> Us</h2>
  <p class="sec-lead" style="left:10px;top:1640px;width:160px;font-size:6px;line-height:10px">Lorem ipsum dolor sit amet, consectetur an adipiscing elit, sed do eiusmod tempor incididunt ut labore man et dolore magna aliqua.</p>
  <div class="field" style="top:1686px">Name</div>
  <div class="field" style="top:1714px">Email Address</div>
  <div class="field" style="top:1743px">Phone Number:</div>
  <div class="field" style="top:1772px">Problem/Issue:</div>
  <div class="field" style="top:1800px;height:58px">Message:</div>
  <div class="btn navy" style="left:10px;top:1864px;width:160px;height:22px;font-size:6px">Send Message</div>

  <footer class="footer" style="top:1905px;width:179px;height:529px">
    <div class="mark light abs" style="left:0;width:179px;justify-content:center;top:37px;font-size:10px">Brightmoor Lift Inc</div>
    <div class="about" style="left:10px;top:67px;width:160px;height:100px;text-align:center;padding:18px 14px 0">
      <h4 style="font-size:6.5px;margin-bottom:10px">About Us</h4>
      <p style="font-size:6px;line-height:10px">Lorem ipsum dolor sit amet, consectetur adipiscing elit, sed do eiusmod tempor incididunt ut labore et dolore magna aliqua.</p>
    </div>
    <div class="f-col" style="left:24px;top:194px;font-size:6px">
      <h4 style="font-size:8.5px;margin-bottom:12px">Quick Links</h4>
      <ul style="line-height:15.3px"><li>Home</li><li>Our Services</li><li>Employees</li><li>FAQs</li><li>Free Quote</li><li>Contact Us</li></ul>
    </div>
    <div class="f-col" style="left:114px;top:194px;font-size:6px">
      <h4 style="font-size:8.5px;margin-bottom:12px">Others</h4>
      <ul style="line-height:15.3px"><li>Lorem ipsum</li><li>Printing</li><li>Typesetting</li></ul>
    </div>
    <div class="f-col" style="left:24px;top:333px"><h4 style="font-size:8.5px">Contact Info</h4></div>
    <div class="contact-row" style="left:24px;top:360px;gap:14px;font-size:6px">
      <svg width="8" height="8" viewBox="0 0 10 10"><path d="M2 1l2 2-1 1.3c.6 1.2 1.5 2.1 2.7 2.7L7 6l2 2-1.2 1.2C4.5 9 1 5.5.8 2.2z" fill="#c8283a"/></svg>555-0142-338</div>
    <div class="contact-row" style="left:24px;top:383px;gap:14px;font-size:6px">
      <svg width="8" height="8" viewBox="0 0 10 10"><path d="M1 3c2-2 6-2 8 0l-1 1.5L6.5 4V3h-3v1L2 4.5zM2 5h6l1 4H1z" fill="#c8283a"/></svg>(555) 0196-274</div>
    <div class="contact-row" style="left:24px;top:406px;gap:14px;font-size:6px">
      <svg width="8" height="8" viewBox="0 0 10 10"><rect x="0.5" y="2" width="9" height="6.5" fill="#c8283a"/><path d="M1 2.5l4 3 4-3" stroke="#0e0d2e" stroke-width=".8" fill="none"/></svg>service@brightmoorlift.com</div>
    <div class="contact-row" style="left:24px;top:431px;gap:14px;font-size:6px;line-height:9px">
      <svg width="8" height="10" viewBox="0 0 8 10"><path d="M4 0a3.5 3.5 0 0 1 3.5 3.5C7.5 6 4 10 4 10S.5 6 .5 3.5A3.5 3.5 0 0 1 4 0z" fill="#c8283a"/><circle cx="4" cy="3.5" r="1.2" fill="#0e0d2e"/></svg>
      <span>Unit 12, 88 Harrowgate<br>Road, Suite 4 ON 0000</span></div>
    <div class="abs" style="left:0;top:485px;width:179px;height:1px;background:var(--divider)"></div>
    <p class="abs" style="left:0;top:495px;width:179px;text-align:center;font-size:6px;line-height:10px">© Copyright 2020. Brightmoor Lift INC<br>Privacy and Policy.</p>
  </footer>
</section>

<section class="board desktop" aria-label="Desktop layout">
  <header>
    <div class="abs" style="left:94px;top:10px;width:22px;height:22px;border:1px solid var(--red);border-radius:50%;display:flex;align-items:center;justify-content:center">
      <svg width="9" height="7" viewBox="0 0 10 8"><rect width="10" height="8" rx="1" fill="#c8283a"/><path d="M1 1l4 3 4-3" stroke="#fff" stroke-width=".9" fill="none"/></svg>
    </div>
    <div class="topline" style="left:124px;top:10px"><div class="label">Drop Us Email</div><div style="margin-top:1px">service@brightmoorlift.com</div></div>
    <div class="mark abs" style="left:282px;width:200px;justify-content:center;top:12px;font-size:14px">Brightmoor Lift Inc</div>
    <div class="topline" style="right:128px;top:10px;text-align:right"><div class="label">Make A Call</div><div style="margin-top:1px">555-0142-3380</div></div>
    <div class="abs" style="left:648px;top:10px;width:22px;height:22px;border:1px solid var(--red);border-radius:50%;display:flex;align-items:center;justify-content:center">
      <svg width="9" height="9" viewBox="0 0 10 10"><path d="M2 1l2 2-1 1.3c.6 1.2 1.5 2.1 2.7 2.7L7 6l2 2-1.2 1.2C4.5 9 1 5.5.8 2.2z" fill="#c8283a"/></svg>
    </div>
    <nav class="nav">
      <span class="active">Home</span><span>Our Services</span><span>Employees</span><span>FAQs</span><span>Free Quote</span><span>Contact Us</span>
    </nav>
  </header>

  <div class="photo hero-photo" role="img" aria-label="Looking up at tall glass office towers against a blue sky" style="left:0;top:81px;width:764px;height:406px"></div>
  <div class="tag red" style="left:96px;top:162px;width:90px;height:28px;font-size:14px;font-weight:700">Welcome</div>
  <div class="tag navy" style="left:96px;top:194px;width:363px;height:50px;font-size:33px;font-weight:800;letter-spacing:2px">Brightmoor Lift</div>
  <div class="tag red" style="left:96px;top:246px;width:90px;height:50px;font-size:33px;font-weight:800;letter-spacing:2px">INC</div>
  <div class="btn navy" style="left:96px;top:330px;width:86px;height:29px;font-size:8.5px">Free Quote</div>
  <div class="btn red" style="left:187px;top:330px;width:86px;height:29px;font-size:8.5px">Contact Us</div>

  <h2 class="sec-title" style="top:542px;font-size:27px"><em>Services</em> We Offer</h2>
  <p class="sec-lead" style="left:207px;top:582px;width:350px;font-size:8.5px;line-height:13px">Lorem ipsum dolor sit amet, consectetur an adipiscing elit, sed do eiusmod tempor incididunt ut labore man et dolore magna aliqua.</p>

  <article class="card" style="left:120px;top:628px;width:250px;height:277px">
    <div class="pic pic-modern" role="img" aria-label="Modern building lobby at night" style="height:114px"></div>
    <h3>Modernization</h3>
    <p>Lorem ipsum dolor sit amet, consectetur adipiscing elit, sed do eiusmod tempor incididunt ut labore et dolore magna aliqua. Ut enim ad minim veniam, quis nostrud exercitation...</p>
    <span class="more">Free Quote</span>
  </article>
  <article class="card" style="left:394px;top:628px;width:250px;height:277px">
    <div class="pic pic-maint" role="img" aria-label="Technician working on a glass facade" style="height:114px"></div>
    <h3>Maintenance</h3>
    <p>Lorem ipsum dolor sit amet, consectetur adipiscing elit, sed do eiusmod tempor incididunt ut labore et dolore magna aliqua. Ut enim ad minim veniam, quis nostrud exercitation...</p>
    <span class="more">Free Quote</span>
  </article>
  <article class="card" style="left:120px;top:926px;width:250px;height:279px">
    <div class="pic pic-repair" role="img" aria-label="Wall rack of wrenches" style="height:114px"></div>
    <h3>Repairing</h3>
    <p>Lorem ipsum dolor sit amet, consectetur adipiscing elit, sed do eiusmod tempor incididunt ut labore et dolore magna aliqua. Ut enim ad minim veniam, quis nostrud exercitation...</p>
    <span class="more">Free Quote</span>
  </article>
  <article class="card" style="left:394px;top:926px;width:250px;height:279px">
    <div class="pic pic-other" role="img" aria-label="Red ratchet tools on a workbench" style="height:114px"></div>
    <h3>Other Services</h3>
    <p>Lorem ipsum dolor sit amet, consectetur adipiscing elit, sed do eiusmod tempor incididunt ut labore et dolore magna aliqua. Ut enim ad minim veniam, quis nostrud exercitation...</p>
    <span class="more">Free Quote</span>
  </article>

  <div class="abs" style="left:0;top:1266px;width:764px;height:614px;background:var(--soft)"></div>
  <h2 class="sec-title" style="top:1322px;font-size:27px"><em>Our Project</em> Gallery</h2>
  <p class="sec-lead" style="left:207px;top:1370px;width:350px;font-size:8.5px;line-height:13px">Lorem ipsum dolor sit amet, consectetur an adipiscing elit, sed do eiusmod tempor incididunt ut labore man et dolore magna aliqua.</p>
  <div class="gallery" style="left:96px;top:1415px;width:573px;height:405px;grid-template-columns:repeat(3,1fr);grid-template-rows:1fr 1fr">
    <div class="g1" role="img" aria-label="Elevator lobby with wood panelling"></div>
    <div class="g2" role="img" aria-label="Downtown skyscrapers"></div>
    <div class="g3" role="img" aria-label="Warm-lit elevator hallway"></div>
    <div class="g4" role="img" aria-label="Residential tower balconies"></div>
    <div class="g5" role="img" aria-label="Apartment block facade"></div>
    <div class="g-cta" style="font-size:21px;line-height:33px">View Project<br>Detail</div>
  </div>

  <h2 class="sec-title" style="top:1934px;font-size:27px"><em>Contact</em> Us</h2>
  <p class="sec-lead" style="left:207px;top:1982px;width:350px;font-size:8.5px;line-height:13px">Lorem ipsum dolor sit amet, consectetur an adipiscing elit, sed do eiusmod tempor incididunt ut labore man et dolore magna aliqua.</p>
  <div class="field" style="left:137px;top:2031px;width:231px">Name:</div>
  <div class="field" style="left:396px;top:2031px;width:231px">Email Address:</div>
  <div class="field" style="left:137px;top:2070px;width:231px">Phone Number:</div>
  <div class="field" style="left:396px;top:2070px;width:231px">Problem/Issue:</div>
  <div class="field" style="left:137px;top:2110px;width:490px;height:79px">Message:</div>
  <div class="btn navy" style="left:340px;top:2215px;width:85px;height:30px;font-size:8.5px">Send Message</div>

  <footer class="footer" style="top:2307px;width:764px;height:244px">
    <div class="mark light abs" style="left:96px;top:46px;font-size:17px">Brightmoor Lift Inc</div>
    <div class="about" style="left:96px;top:104px;width:160px;height:84px;padding:12px 12px 0">
      <h4 style="font-size:8px;margin-bottom:6px">About Us</h4>
      <p style="font-size:7.5px;line-height:11.5px">Lorem ipsum dolor sit amet, consectetur adipiscing elit, sed do eiusmod tempor incididunt ut labore et dolore magna aliqua.</p>
    </div>
    <div class="f-col" style="left:303px;top:40px;font-size:8.5px">
      <h4 style="font-size:12px;margin-bottom:24px">Quick Links</h4>
      <ul style="line-height:19.6px"><li>Home</li><li>Our Services</li><li>Employees</li><li>FAQs</li><li>Free Quote</li><li>Contact Us</li></ul>
    </div>
    <div class="f-col" style="left:440px;top:40px;font-size:8.5px">
      <h4 style="font-size:12px;margin-bottom:24px">Others</h4>
      <ul style="line-height:19.6px"><li>Lorem ipsum</li><li>Printing</li><li>Typesetting</li></ul>
    </div>
    <div class="f-col" style="left:558px;top:42px"><h4 style="font-size:12px">Contact Info</h4></div>
    <div class="contact-row" style="left:558px;top:77px;gap:15px;font-size:8.5px">
      <svg width="10" height="10" viewBox="0 0 10 10"><path d="M2 1l2 2-1 1.3c.6 1.2 1.5 2.1 2.7 2.7L7 6l2 2-1.2 1.2C4.5 9 1 5.5.8 2.2z" fill="#c8283a"/></svg>555-0142-338</div>
    <div class="contact-row" style="left:558px;top:100px;gap:15px;font-size:8.5px">
      <svg width="10" height="10" viewBox="0 0 10 10"><path d="M1 3c2-2 6-2 8 0l-1 1.5L6.5 4V3h-3v1L2 4.5zM2 5h6l1 4H1z" fill="#c8283a"/></svg>(555) 0196-274</div>
    <div class="contact-row" style="left:558px;top:123px;gap:15px;font-size:8.5px">
      <svg width="10" height="10" viewBox="0 0 10 10"><rect x="0.5" y="2" width="9" height="6.5" fill="#c8283a"/><path d="M1 2.5l4 3 4-3" stroke="#0e0d2e" stroke-width=".8" fill="none"/></svg>service@brightmoorlift.com</div>
    <div class="contact-row" style="left:558px;top:148px;gap:15px;font-size:8.5px;line-height:14px">
      <svg width="10" height="12" viewBox="0 0 8 10"><path d="M4 0a3.5 3.5 0 0 1 3.5 3.5C7.5 6 4 10 4 10S.5 6 .5 3.5A3.5 3.5 0 0 1 4 0z" fill="#c8283a"/><circle cx="4" cy="3.5" r="1.2" fill="#0e0d2e"/></svg>
      <span>Unit 12, 88<br>Harrowgate Road, Suite 4<br>ON 0000</span></div>
    <div class="abs" style="left:0;top:218px;width:764px;height:1px;background:var(--divider)"></div>
    <p class="abs" style="left:96px;top:227px;font-size:8px">Privacy and Policy.</p>
    <p class="abs" style="right:95px;top:227px;font-size:8px">© Copyright 2020. Brightmoor Lift INC</p>
  </footer>
</section>

</body>
</html>
```